Roadside building business signage for a holistic health clinic.

Replace signs as shown in the attached file. They are perforated stickers that go on the windows as shown. Looking for something that has our logo and says the name of the practice with logo (Fernridge Health & Wellness) also boldly says Acupuncture, IV Vitamins, and Holistic Health.
Possibly our phone number as well 318-562-7041
Updates

Please don't use pink except the logo. Earthy, organic tone colors appreciated.

Need of eye catching window signage of a holistic clinic on a brick building. Pink, purple, sage green, white color. Logo is pink on a white background. Please don't overload with too much pink. Words to include are "Fernridge Health and Wellness(name of business)", "Direct Primary Care", " Medical acupuncture", "IV Vitamin Therapy", "fernridgecareclinic.example","318-562-7041".

Target Market(s)

People will see in their cars passing by the building. Busy roadside so need to be visible while passing in fast speed.

Industry/Entity Type

Health & Wellness

Font styles to use
Sans Serif

Colors

Designer to choose colors to be used in the design.

Requirements
Must have
• On sign must have words Holistic Medicine, Medical Acupuncture, Direct Primary Care and IV vitamins.
Nice to have
• Simple, minimalistic, artistic yet has clear message. White, Black, Violet, Pink (logo), Dark green, Sage green.
Should not have
• Bold colors (red, yellow, blue), same tone colors. Blue waves on the current signage (uploaded file) must go.

```html
<!DOCTYPE html>
<html lang="en">
<head>
<meta charset="utf-8">
<title>Fernridge Health &amp; Wellness – Window Signage</title>
<link rel="stylesheet" href="https://fonts.googleapis.com/css2?family=Poppins:wght@300;500;600;700&display=swap">
<style>
  :root {
    --backdrop: #ebebeb;
    --sage: #5f8b72;
    --sage-faint: #7aa28a;
    --forest: #1f4d3d;
    --plum: #7a2c4f;
    --lavender: #cfc4d8;
    --cream: #f6ecd3;
    --cream-light: #fffcf4;
    --ink: #1c1c1c;
    --blossom: #e2559b;
  }
  * { margin: 0; padding: 0; box-sizing: border-box; }
  html, body { width: 1200px; height: 2934px; overflow: hidden; }
  body { background: var(--backdrop); position: relative; font-family: "Poppins", sans-serif; }
  .decal { position: absolute; width: 520px; height: 520px; filter: drop-shadow(0 2px 4px rgba(0,0,0,.18)); }
  .decal svg { display: block; width: 100%; height: 100%; }
  .decal--arch { left: 380px; top: 307px; }
  .decal--brand { left: 60px; top: 907px; }
  .decal--services { left: 620px; top: 907px; }
  .decal--primary-care { left: 60px; top: 1507px; }
  .decal--wave { left: 620px; top: 1507px; }
  .decal--corner { left: 340px; top: 2107px; }
  .wave-edge { fill: none; stroke: var(--cream-light); stroke-width: 26; }
  .wave-stripe { fill: none; stroke: var(--lavender); stroke-width: 12; }
  .faint-name { font-family: "Poppins", sans-serif; font-weight: 300; font-size: 40px; letter-spacing: 6px; fill: var(--sage-faint); opacity: .55; }
  .headline { font-family: "Poppins", sans-serif; font-weight: 600; font-size: 38px; fill: var(--ink); }
  .brand-name { font-family: "Poppins", sans-serif; font-weight: 500; fill: var(--forest); }
  .brand-web { font-family: "Poppins", sans-serif; font-weight: 600; font-size: 24px; letter-spacing: 1.5px; fill: var(--ink); }
  .service-label { font-family: "Poppins", sans-serif; font-weight: 600; font-size: 29px; fill: var(--ink); }
  .contact-line { font-family: "Poppins", sans-serif; font-weight: 600; fill: #fff; }
  .leader { stroke: #b79aa8; stroke-width: 1.5; fill: none; }
</style>
</head>
<body>

<svg width="0" height="0" style="position:absolute">
  <defs>
    <radialGradient id="parchment" cx="45%" cy="40%" r="75%">
      <stop offset="0" stop-color="var(--cream-light)"/>
      <stop offset=".55" stop-color="#faf3e2"/>
      <stop offset="1" stop-color="var(--cream)"/>
    </radialGradient>
    <linearGradient id="foliage" x1="0" y1="0" x2="1" y2="1">
      <stop offset="0" stop-color="#8fae8a"/>
      <stop offset="1" stop-color="#c9d7bf" stop-opacity="0"/>
    </linearGradient>
    <clipPath id="arch-shape"><path d="M0,0 H40 C260,10 470,200 515,520 H0 Z"/></clipPath>
  </defs>
</svg>

<!-- Arch top -->
<div class="decal decal--arch">
  <svg viewBox="0 0 520 520">
    <g clip-path="url(#arch-shape)">
      <rect width="520" height="520" fill="url(#parchment)"/>
      <path d="M0,0 H260 L225,55 C185,85 172,120 170,165 C168,222 132,262 82,282 C42,298 12,312 0,330 Z" fill="var(--sage)"/>
      <path class="wave-edge" d="M240,40 L225,55 C185,85 172,120 170,165 C168,222 132,262 82,282 C42,298 12,312 0,330"/>
      <path class="wave-stripe" d="M240,40 L225,55 C185,85 172,120 170,165 C168,222 132,262 82,282 C42,298 12,312 0,330" transform="translate(6,6)"/>
    </g>
  </svg>
</div>

<!-- Brand panel -->
<div class="decal decal--brand">
  <svg viewBox="0 0 520 520">
    <rect width="520" height="520" fill="url(#parchment)"/>
    <circle cx="260" cy="150" r="48" fill="var(--blossom)"/>
    <text class="brand-name" x="260" y="278" text-anchor="middle" font-size="66" letter-spacing="8">FERNRIDGE</text>
    <text class="brand-name" x="260" y="318" text-anchor="middle" font-size="20" letter-spacing="9">HEALTH &amp; WELLNESS</text>
    <text class="brand-web" x="260" y="448" text-anchor="middle">www.fernridgecareclinic.example</text>
  </svg>
</div>

<!-- Services panel -->
<div class="decal decal--services">
  <svg viewBox="0 0 520 520">
    <rect width="520" height="520" fill="url(#parchment)"/>
    <path role="img" aria-label="Eucalyptus sprig trailing from the top corner" d="M0,0 H140 C130,60 110,120 80,170 C55,150 20,120 0,110 Z" fill="url(#foliage)"/>
    <path class="leader" d="M120,118 H170 M254,98 L280,78 H520 M254,148 L280,168 H510 M40,280 H246 M40,180 H246 M255,310 L280,288 H510 M255,355 L285,385 H510"/>
    <polygon points="212,81 248,102 248,144 212,165 176,144 176,102" fill="var(--sage)"/>
    <polygon points="212,88 242,106 242,140 212,158 182,140 182,106" fill="none" stroke="#fff" stroke-width="1.5" stroke-dasharray="4 3"/>
    <polygon points="289,185 325,206 325,248 289,269 253,248 253,206" fill="var(--plum)"/>
    <polygon points="289,192 319,210 319,244 289,262 259,244 259,210" fill="none" stroke="#fff" stroke-width="1.5" stroke-dasharray="4 3"/>
    <polygon points="212,285 248,306 248,348 212,369 176,348 176,306" fill="var(--sage)"/>
    <polygon points="212,292 242,310 242,344 212,362 182,344 182,310" fill="none" stroke="#fff" stroke-width="1.5" stroke-dasharray="4 3"/>
    <text class="service-label" x="278" y="134">Acupuncture</text>
    <text class="service-label" x="228" y="238" text-anchor="end">IV Vitamins</text>
    <text class="service-label" x="276" y="338">Holistic Health</text>
    <rect y="430" width="520" height="5" fill="var(--plum)"/>
    <rect y="441" width="520" height="79" fill="var(--sage)"/>
    <path d="M20,478 c3,-3 6,-3 8,0 l3,4 c1,2 0,4 -2,5 c2,5 6,9 11,11 c1,-2 3,-3 5,-2 l4,3 c3,2 3,5 0,8 c-4,4 -12,2 -20,-6 c-8,-8 -11,-17 -9,-23 z" fill="none" stroke="#fff" stroke-width="2.2"/>
    <text class="contact-line" x="44" y="496" font-size="25" letter-spacing="1">318-562-7041</text>
    <g fill="none" stroke="#fff" stroke-width="1.8">
      <circle cx="260" cy="488" r="8"/>
      <ellipse cx="260" cy="488" rx="3.5" ry="8"/>
      <path d="M252,488 H268"/>
    </g>
    <text class="contact-line" x="274" y="494" font-size="15" textLength="228" lengthAdjust="spacingAndGlyphs">fernridgecareclinic.example</text>
  </svg>
</div>

<!-- Direct primary care panel -->
<div class="decal decal--primary-care">
  <svg viewBox="0 0 520 520">
    <rect width="520" height="520" fill="url(#parchment)"/>
    <path d="M0,0 H520 V230 C470,235 420,250 390,270 C350,300 310,310 290,295 C260,270 240,235 200,240 C150,245 110,230 80,195 C50,160 20,110 0,95 Z" fill="var(--sage)"/>
    <path class="wave-edge" d="M520,230 C470,235 420,250 390,270 C350,300 310,310 290,295 C260,270 240,235 200,240 C150,245 110,230 80,195 C50,160 20,110 0,95"/>
    <path class="wave-stripe" d="M520,230 C470,235 420,250 390,270 C350,300 310,310 290,295 C260,270 240,235 200,240 C150,245 110,230 80,195 C50,160 20,110 0,95" transform="translate(0,14)"/>
    <text class="faint-name" x="262" y="150" text-anchor="middle">FERNRIDGE</text>
    <text class="headline" x="260" y="392" text-anchor="middle">DIRECT</text>
    <text class="headline" x="260" y="438" text-anchor="middle">PRIMARY CARE</text>
    <rect y="506" width="520" height="14" fill="var(--sage)"/>
  </svg>
</div>

<!-- Wave panel -->
<div class="decal decal--wave">
  <svg viewBox="0 0 520 520">
    <rect width="520" height="520" fill="url(#parchment)"/>
    <path d="M0,0 H520 V95 C470,110 440,170 400,230 C350,300 280,330 220,300 C160,270 110,190 70,130 C45,100 20,90 0,95 Z" fill="var(--sage)"/>
    <path class="wave-edge" d="M520,95 C470,110 440,170 400,230 C350,300 280,330 220,300 C160,270 110,190 70,130 C45,100 20,90 0,95"/>
    <path class="wave-stripe" d="M520,95 C470,110 440,170 400,230 C350,300 280,330 220,300 C160,270 110,190 70,130 C45,100 20,90 0,95" transform="translate(0,14)"/>
    <text class="faint-name" x="262" y="160" text-anchor="middle">FERNRIDGE</text>
    <rect y="506" width="520" height="14" fill="var(--sage)"/>
  </svg>
</div>

<!-- Corner panel -->
<div class="decal decal--corner">
  <svg viewBox="0 0 520 520">
    <rect width="520" height="520" fill="url(#parchment)"/>
    <path d="M0,0 H520 C510,60 500,110 470,150 C430,200 380,210 330,230 C270,250 230,300 180,330 C130,360 90,340 60,360 C30,380 15,400 0,410 Z" fill="var(--sage)"/>
    <path class="wave-edge" d="M520,0 C510,60 500,110 470,150 C430,200 380,210 330,230 C270,250 230,300 180,330 C130,360 90,340 60,360 C30,380 15,400 0,410"/>
    <path class="wave-stripe" d="M520,0 C510,60 500,110 470,150 C430,200 380,210 330,230 C270,250 230,300 180,330 C130,360 90,340 60,360 C30,380 15,400 0,410" transform="translate(0,14)"/>
    <text class="faint-name" x="175" y="160" text-anchor="middle">FERNRIDGE</text>
    <rect y="506" width="520" height="14" fill="var(--sage)"/>
  </svg>
</div>

</body>
</html>
```